its a new company based in Christchurch new Zealand building computers ,repairs, upgrades and anything computers for the general public,i like bright happy colours like yellows, greens reds anything that stands out and it needs to communicant trust and security towards my new company,i have no logo yet,

Target Market(s)

target market of all ages

Industry/Entity Type

Building

Contact Information for Business Card

Byte Harbour Limited,ph-0218847261,email-tidelark77@mailvesta.test,14c marlowe cres,fenwick

```html
<!DOCTYPE html>
<html lang="en">
<head>
<meta charset="utf-8">
<title>Byte Harbour Limited – Business Card</title>
<link rel="stylesheet" href="https://fonts.googleapis.com/css2?family=Exo+2:wght@400;600;700&display=swap">
<style>
  :root{
    --bg:#e9eaec;
    --brand-blue:#2aa7df;
    --brand-purple:#7b4d93;
    --paper:#f4f4f4;
    --white:#ffffff;
    --charcoal:#3a3b3e;
    --charcoal-dark:#2b2c2e;
    --slate:#55575b;
  }
  *{box-sizing:border-box;margin:0;padding:0}
  html,body{width:1200px;height:974px;overflow:hidden;background:var(--bg)}
  body{font-family:"Exo 2",sans-serif;position:relative}

  .card{position:absolute;top:167px;width:400px;height:640px;box-shadow:0 10px 30px rgba(0,0,0,.18)}

  /* Front */
  .card-front{left:150px;background:var(--brand-blue);padding:14px}
  .front-frame{width:100%;height:100%;background:var(--brand-purple);padding:14px}
  .front-face{width:100%;height:100%;background:var(--paper);position:relative}
  .front-brand{position:absolute;top:110px;left:0;right:0;display:flex;justify-content:center;align-items:center;gap:10px}
  .brand-mark{width:16px;height:16px;border-radius:50%;background:var(--brand-blue)}
  .brand-name{font-weight:700;font-size:25px;color:var(--brand-blue);letter-spacing:.3px}

  /* Back */
  .card-back{left:650px;background:var(--white);padding:16px}
  .back-face{position:relative;width:368px;height:608px;overflow:hidden;background:var(--charcoal)}
  .back-shapes{position:absolute;inset:0}
  .back-brand{position:absolute;top:64px;left:0;right:0;display:flex;justify-content:center;align-items:center;gap:10px}
  .holder{position:absolute;top:290px;left:34px;color:var(--white)}
  .holder-name{font-weight:700;font-size:30px;letter-spacing:1.5px;text-transform:uppercase}
  .holder-role{font-weight:400;font-size:15px;letter-spacing:2.5px;text-transform:uppercase;margin-top:2px}
  .contact-list{position:absolute;top:378px;left:34px;list-style:none;color:var(--white);font-size:14px;letter-spacing:.8px}
  .contact-list li{display:flex;align-items:center;gap:12px;height:24px}
  .contact-list svg{width:15px;height:15px;fill:var(--white)}
  .address{position:absolute;top:540px;left:24px;display:flex;gap:12px;align-items:flex-start;color:var(--white);font-size:14px;letter-spacing:.8px;line-height:1.45}
  .address-pin{width:26px;height:26px;border-radius:50%;background:var(--white);display:flex;align-items:center;justify-content:center;margin-top:3px}
  .address-pin svg{width:14px;height:14px;fill:var(--charcoal)}
</style>
</head>
<body>

<section class="card card-front" aria-label="Business card front">
  <div class="front-frame">
    <div class="front-face">
      <div class="front-brand">
        <span class="brand-mark"></span>
        <span class="brand-name">Byte Harbour Limited</span>
      </div>
    </div>
  </div>
</section>

<section class="card card-back" aria-label="Business card back">
  <div class="back-face">
    <svg class="back-shapes" viewBox="0 0 368 608" preserveAspectRatio="none" aria-hidden="true">
      <polygon points="0,250 368,150 368,178 0,278" fill="var(--slate)"/>
      <polygon points="0,262 368,182 368,196 0,276" fill="var(--brand-blue)"/>
      <polygon points="0,282 368,200 368,212 0,294" fill="var(--charcoal-dark)"/>
      <polygon points="0,298 368,216 368,520 0,520" fill="var(--brand-blue)"/>
      <polygon points="0,520 368,520 368,608 0,608" fill="var(--charcoal-dark)"/>
      <polygon points="0,520 368,500 368,520" fill="var(--charcoal-dark)"/>
    </svg>

    <div class="back-brand">
      <span class="brand-mark"></span>
      <span class="brand-name">Byte Harbour Limited</span>
    </div>

    <div class="holder">
      <p class="holder-name">Liam Carter</p>
      <p class="holder-role">General Manager</p>
    </div>

    <ul class="contact-list">
      <li><svg viewBox="0 0 24 24"><path d="M6.6 10.8a15.1 15.1 0 0 0 6.6 6.6l2.2-2.2c.3-.3.7-.4 1-.2 1.1.4 2.3.6 3.6.6.6 0 1 .4 1 1V20c0 .6-.4 1-1 1A17 17 0 0 1 3 4c0-.6.4-1 1-1h3.5c.6 0 1 .4 1 1 0 1.3.2 2.5.6 3.6.1.3 0 .7-.2 1z"/></svg>0218847261</li>
      <li><svg viewBox="0 0 24 24"><path d="M7 1h10a2 2 0 0 1 2 2v18a2 2 0 0 1-2 2H7a2 2 0 0 1-2-2V3a2 2 0 0 1 2-2zm0 3v14h10V4zm5 15.5a1 1 0 1 0 0 2 1 1 0 0 0 0-2z"/></svg>0218847261</li>
      <li><svg viewBox="0 0 24 24"><path d="M2 5h20v14H2zm2 2v.5l8 5 8-5V7zm0 2.9V17h16V9.9l-8 5z"/></svg>tidelark77@mailvesta.test</li>
      <li><svg viewBox="0 0 24 24"><path d="M12 2a10 10 0 1 0 0 20 10 10 0 0 0 0-20zm6.9 9h-3a15 15 0 0 0-1.3-5.6A8 8 0 0 1 18.9 11zM12 4.1c.9 1.3 1.7 3.8 1.9 6.9h-3.8c.2-3.1 1-5.6 1.9-6.9zM9.4 5.4A15 15 0 0 0 8.1 11h-3a8 8 0 0 1 4.3-5.6zM5.1 13h3a15 15 0 0 0 1.3 5.6A8 8 0 0 1 5.1 13zm6.9 6.9c-.9-1.3-1.7-3.8-1.9-6.9h3.8c-.2 3.1-1 5.6-1.9 6.9zm2.6-1.3a15 15 0 0 0 1.3-5.6h3a8 8 0 0 1-4.3 5.6z"/></svg>www.byteharbour.test</li>
    </ul>

    <div class="address">
      <span class="address-pin"><svg viewBox="0 0 24 24"><path d="M12 2a7 7 0 0 0-7 7c0 5 7 13 7 13s7-8 7-13a7 7 0 0 0-7-7zm0 9.5a2.5 2.5 0 1 1 0-5 2.5 2.5 0 0 1 0 5z"/></svg></span>
      <p>14c marlowe cres,<br>fenwick</p>
    </div>
  </div>
</section>

</body>
</html>
```